Luxury travel agency needs a website design

We are a travel agency specializing in booking luxury vacations. We specialize in Hawaii, Europe and Caribbean, but will do all vacations. I want a very classy website design which would attract luxury clients. The company name is "Harbors and Hammocks Travel Agency". Would love the web design to go with the color scheme of the logo. Hex codes included in files. Logo is attached. Would also love more Grey in the website. I want it very elegant

Coding

Coded - Design and coding required

Font styles to use
Sans Serif
Decorative

Requirements
Must have
• - Consultation Tab or a page where the client can fill out a short form about what vacation that they would want to book. I want this info to be sent to me in order for me to contact them.
- Somewhere with my contact info "email: marla@harborsandhammockstravel.example and phone number"
- Social media links
- About section "Marla Dunbevy - Agency Owner (picture provided)
Marla has been traveling full time for the passed two years and has been very passionate about travel from a young age. Marla is dedicated to working closely with clients to book their dream vacation.
Marla's specializations include honeymoons and anniversaries focusing on travel in Europe, Hawaii and all inclusive resorts in the Caribbean.

```html
<!DOCTYPE html>
<html lang="en">
<head>
<meta charset="utf-8">
<title>Harbors and Hammocks Travel Agency</title>
<link rel="stylesheet" href="https://fonts.googleapis.com/css2?family=Bubblegum+Sans&family=Lobster&family=Montserrat:wght@600;700&family=Open+Sans:wght@400;600;700&family=Lato:wght@400&display=swap">
<style>
:root{
  --orange:#ee7048;
  --orange-deep:#e8693f;
  --yellow:#f4c158;
  --ink:#2f3033;
  --grey:#34373b;
  --text:#4a4a4a;
  --muted:#8a8a8a;
  --white:#ffffff;
  --line:#e6e6e6;
}
*{margin:0;padding:0;box-sizing:border-box}
html,body{width:1200px;height:3692px;overflow:hidden;background:var(--white)}
body{position:relative;font-family:"Open Sans",Arial,sans-serif;color:var(--text)}
.abs{position:absolute}
.deco{font-family:"Lobster",cursive;font-weight:400}

/* header */
.site-header{left:0;top:0;width:1200px;height:84px;background:var(--white);z-index:5}
.nav-link{font-family:"Bubblegum Sans",sans-serif;font-size:19px;color:var(--ink);top:42px;text-transform:uppercase;letter-spacing:.3px}
.nav-link.active{color:var(--orange)}
.brand-disc{left:475px;top:-100px;width:250px;height:250px;border-radius:50%;background:var(--white);z-index:4}
.brand{left:475px;top:40px;width:250px;text-align:center;z-index:6;font-family:"Bubblegum Sans",sans-serif;font-size:20px;line-height:22px;color:var(--ink)}
.brand-dot{display:block;margin:0 auto 6px;width:22px;height:22px;border-radius:50%;background:var(--yellow)}

/* hero */
.hero{left:0;top:84px;width:1200px;height:728px;background:linear-gradient(100deg,#2f7fb8 0%,#58a9d6 28%,#e9eef2 50%,#d8dde0 70%,#b9c2c6 100%)}
.hero-panel{left:0;top:350px;width:698px;height:220px;background:rgba(70,70,72,.6)}
.hero-title{left:110px;top:362px;font-size:38px;color:var(--white);letter-spacing:.5px}
.hero-text{left:110px;top:416px;width:580px;font-size:16px;line-height:29px;color:var(--white)}
.btn{top:493px;height:50px;border-radius:25px;font-weight:700;font-size:16px;letter-spacing:.5px;display:flex;align-items:center;justify-content:center;text-transform:uppercase}
.btn-book{left:112px;width:152px;background:var(--yellow);color:var(--ink)}
.btn-consult{left:275px;width:178px;background:var(--orange);color:var(--white)}

/* about */
.portrait{left:112px;top:896px;width:510px;height:510px;border-radius:50%;background:radial-gradient(circle at 50% 45%,#8a6a58 0%,#6d4c3c 45%,#56a9c4 80%,#7a7f7a 100%);box-shadow:0 2px 8px rgba(0,0,0,.25)}
.about-title{left:655px;top:1000px;font-size:40px;color:var(--orange)}
.about-copy{left:657px;top:1075px;width:440px;font-size:15px;line-height:29px;color:var(--text)}
.about-copy p+p{margin-top:19px}

/* destinations */
.section-title{left:0;width:1200px;text-align:center;font-size:42px}
.dest{overflow:hidden}
.dest-label{right:0;bottom:0;width:172px;height:53px;background:var(--orange);color:var(--white);font-size:16px;display:flex;align-items:center;justify-content:center;text-transform:uppercase}

/* how it works */
.how{left:0;top:2188px;width:1200px;height:417px;background:linear-gradient(180deg,#3a3c40,#303236)}
.how-title{top:80px;color:var(--white);font-size:38px}
.step{top:160px;width:300px;text-align:center;color:var(--white)}
.step svg{display:block;margin:0 auto}
.step h3{font-size:27px;font-weight:700;letter-spacing:1.5px;margin-top:14px}
.step p{font-size:14px;line-height:26px;margin-top:12px}

/* blog */
.blog-card{top:2757px;width:476px;height:495px;border:1px solid var(--line);background:var(--white);box-shadow:0 1px 4px rgba(0,0,0,.06)}
.blog-img{position:absolute;left:11px;top:11px;width:454px;height:232px}
.blog-title{position:absolute;left:39px;top:282px;width:410px;font-family:"Montserrat",sans-serif;font-weight:700;font-size:18.5px;line-height:28px;color:var(--ink);letter-spacing:.3px}
.blog-meta{position:absolute;left:39px;top:360px;font-family:"Lato",sans-serif;font-size:14px;color:var(--muted);display:flex;align-items:center;gap:7px}
.blog-excerpt{position:absolute;left:39px;top:404px;width:410px;font-family:"Lato",sans-serif;font-size:13.5px;line-height:25px;color:var(--muted)}

/* footer */
.site-footer{left:0;top:3332px;width:1200px;height:360px;background:var(--orange-deep);color:var(--white)}
.footer-brand{top:66px;left:0;width:1200px;text-align:center;font-family:"Bubblegum Sans",sans-serif;font-size:28px;color:var(--ink)}
.footer-nav{top:186px;left:0;width:1200px;display:flex;justify-content:center;gap:38px;font-family:"Bubblegum Sans",sans-serif;font-size:18px;text-transform:uppercase}
.social{top:236px;left:534px;display:flex;gap:14px}
.social span{width:34px;height:30px;border:1px solid var(--white)}
.legal{top:302px;left:0;width:1200px;display:flex;justify-content:center;gap:14px;font-family:Arial,sans-serif;font-size:14px}
</style>
</head>
<body>

<header class="abs site-header">
  <a class="abs nav-link active" style="left:191px">Home</a>
  <a class="abs nav-link" style="left:261px">About</a>
  <a class="abs nav-link" style="left:338px">Services</a>
  <a class="abs nav-link" style="left:796px">Why Us</a>
  <a class="abs nav-link" style="left:881px">Videos</a>
  <a class="abs nav-link" style="left:959px">Contact</a>
</header>
<div class="abs brand-disc"></div>
<div class="abs brand"><span class="brand-dot"></span>Harbors &amp; Hammocks Travel Agency</div>

<section class="abs hero" role="img" aria-label="Photo of a traveller in a red dress and sun hat overlooking white village houses with blue domes and the sea"></section>
<div class="abs hero-panel"></div>
<h1 class="abs deco hero-title">Let Us Plan Your Dream Vacation!</h1>
<p class="abs hero-text">Lorem ipsum dolor sit amet, consectetur adipiscing elit, sed do eiusmod tempor incididunt ut labore et dolore magna aliqua. Ut enim ad</p>
<a class="abs btn btn-book">Book Now</a>
<a class="abs btn btn-consult">Consultation</a>

<div class="abs portrait" role="img" aria-label="Portrait photo of agency owner Marla Dunbevy"></div>
<h2 class="abs deco about-title">About Marla Dunbevy</h2>
<div class="abs about-copy">
  <p>Marla has been traveling full time for the passed two years and has been very passionate about travel from a young age. Marla is dedicated to working closely with clients to book their dream vacation</p>
  <p>Marla's specializations include honeymoons and anniversaries focusing on travel in Europe, Hawaii and all inclusive resorts in the Caribbean</p>
</div>

<h2 class="abs deco section-title" style="top:1482px;color:var(--orange)">Find Destination</h2>

<div class="abs dest" style="left:0;top:1589px;width:600px;height:300px;background:linear-gradient(135deg,#d9cfc2,#7f9a52 45%,#ece8e0 80%,#8f8a80)" role="img" aria-label="Photo of a whitewashed village lane with round stone-roofed houses">
  <span class="abs dest-label">Italy &raquo;</span></div>
<div class="abs dest" style="left:600px;top:1589px;width:300px;height:300px;background:linear-gradient(180deg,#e9a07a,#5f6f8a 40%,#dcdde2 75%,#8ea0b4)" role="img" aria-label="Photo of a cliffside white town with stairs at sunset">
  <span class="abs dest-label">Greece &raquo;</span></div>
<div class="abs dest" style="left:900px;top:1589px;width:300px;height:300px;background:linear-gradient(180deg,#7ea3c9,#8a6248 50%,#b7b2ad)" role="img" aria-label="Photo of a traditional street with wooden houses and a pagoda">
  <span class="abs dest-label">Japan &raquo;</span></div>
<div class="abs dest" style="left:0;top:1889px;width:300px;height:300px;background:linear-gradient(180deg,#9cc4dd,#5d6f6a 45%,#c9963f 60%,#2e6f8c)" role="img" aria-label="Photo of red cabins on stilts by a fjord below mountains">
  <span class="abs dest-label">Europe &raquo;</span></div>
<div class="abs dest" style="left:300px;top:1889px;width:300px;height:300px;background:linear-gradient(160deg,#c6d6dc,#5a8046 35%,#e6dccb 60%,#55a7a0)" role="img" aria-label="Photo of a green headland above a sandy beach with turquoise waves">
  <span class="abs dest-label">Caribbean &raquo;</span></div>
<div class="abs dest" style="left:600px;top:1889px;width:600px;height:300px;background:linear-gradient(180deg,#3f6fa3,#e99c62 45%,#9a4a28 70%,#6a2f1a)" role="img" aria-label="Photo of desert rock buttes under a sunset sky">
  <span class="abs dest-label">USA &raquo;</span></div>

<section class="abs how">
  <h2 class="abs deco section-title how-title">How Wayfarer Guides Works</h2>
  <div class="abs step" style="left:128px">
    <svg width="64" height="64" viewBox="0 0 64 64" fill="none" stroke="#fff" stroke-width="5" stroke-linecap="round"><circle cx="26" cy="26" r="20"/><line x1="41" y1="41" x2="59" y2="59"/></svg>
    <h3>EXPLORE</h3>
    <p>Lorem ipsum dolor sit amet, consectetur adipiscing elit, sed do eiusmod tempor incididunt ut labore et dolore</p>
  </div>
  <div class="abs step" style="left:450px">
    <svg width="64" height="64" viewBox="0 0 64 64" fill="none" stroke="#fff" stroke-width="5" stroke-linecap="round"><rect x="8" y="28" width="30" height="16" rx="8" transform="rotate(-45 23 36)"/><rect x="26" y="20" width="30" height="16" rx="8" transform="rotate(-45 41 28)"/></svg>
    <h3>CONNECT</h3>
    <p>Lorem ipsum dolor sit amet, consectetur adipiscing elit, sed do eiusmod tempor incididunt ut labore et dolore</p>
  </div>
  <div class="abs step" style="left:771px">
    <svg width="64" height="64" viewBox="0 0 64 64" fill="none" stroke="#fff" stroke-width="4" stroke-linecap="round"><path d="M32 8 L38 26 L56 26 L42 37 L47 55 L32 44 L17 55 L22 37 L8 26 L26 26 Z"/></svg>
    <h3>ENJOY</h3>
    <p>Lorem ipsum dolor sit amet, consectetur adipiscing elit, sed do eiusmod tempor incididunt ut labore et dolore</p>
  </div>
</section>

<h2 class="abs deco section-title" style="top:2676px;color:var(--ink)">Latest Blog</h2>

<article class="abs blog-card" style="left:111px">
  <div class="blog-img" style="background:linear-gradient(180deg,#eef2f4,#7fb7cc 55%,#3f8fb0 75%,#9a7a5a)" role="img" aria-label="Photo of a woman on a rope swing over the sea from a wooden deck"></div>
  <h3 class="blog-title">Lorem ipsum dolor sit amet consectetur adipiscing elit sed do eiusmo</h3>
  <div class="blog-meta">
    <svg width="13" height="13" viewBox="0 0 13 13"><rect x="0" y="2" width="13" height="11" fill="#ee7048"/><rect x="1.5" y="5" width="10" height="6.5" fill="#fff"/></svg>
    <span>April 10,2021 |</span>
    <svg width="14" height="13" viewBox="0 0 14 13"><ellipse cx="7" cy="5.5" rx="7" ry="5.5" fill="#ee7048"/><path d="M2 9 L1 13 L6 10 Z" fill="#ee7048"/></svg>
    <span>&nbsp;Comments</span>
  </div>
  <p class="blog-excerpt">Lorem ipsum dolor sit amet, consectetur adipiscing elit, sed do eiusmod tempor incididunt ut labore et dolore magna aliqua. Quis ipsum suspendi aecenas accumsan lacus vel facilisis.</p>
</article>

<article class="abs blog-card" style="left:613px">
  <div class="blog-img" style="background:linear-gradient(180deg,#5d93d0,#dfe8ee 25%,#4f8a4a 40%,#2fb6b8 60%,#b59a78)" role="img" aria-label="Photo of a wooden pier over turquoise water toward a hillside town"></div>
  <h3 class="blog-title">Lorem ipsum dolor sit amet consectetur adipiscing elit sed do eiusmo</h3>
  <div class="blog-meta">
    <svg width="13" height="13" viewBox="0 0 13 13"><rect x="0" y="2" width="13" height="11" fill="#ee7048"/><rect x="1.5" y="5" width="10" height="6.5" fill="#fff"/></svg>
    <span>April 10,2021 |</span>
    <svg width="14" height="13" viewBox="0 0 14 13"><ellipse cx="7" cy="5.5" rx="7" ry="5.5" fill="#ee7048"/><path d="M2 9 L1 13 L6 10 Z" fill="#ee7048"/></svg>
    <span>&nbsp;Comments</span>
  </div>
  <p class="blog-excerpt">Lorem ipsum dolor sit amet, consectetur adipiscing elit, sed do eiusmod tempor incididunt ut labore et dolore magna aliqua. Quis ipsum suspendi aecenas accumsan lacus vel facilisis.</p>
</article>

<footer class="abs site-footer">
  <div class="abs footer-brand">Harbors &amp; Hammocks Travel Agency</div>
  <nav class="abs footer-nav">
    <a>Home</a><a>About</a><a>Services</a><a>Why Us</a><a>Videos</a><a>Contact Us</a>
  </nav>
  <div class="abs social">
    <span aria-label="Social link"></span><span aria-label="Social link"></span><span aria-label="Social link"></span>
  </div>
  <div class="abs legal">
    <a>Privacy Policy</a><a>Terms &amp; Conditions</a><span>|</span><span style="font-size:12.5px;padding-top:1px">&copy; 2021 All Rights Reserved</span>
  </div>
</footer>

</body>
</html>
```